website refresh/redesign needed for Printing e commerce website

We'd like a website refresh/redesign done with the specific goal of having the site act as a more effective funnel for leads.<br/><br/>We think that the current design is outdated.<br/><br/>We want our customers and partners to still recognize the website, Is a big chunk of our business is repeat orders. <br/>so it should not be a full redesign. General color scheme and such should remain the same so that it is clear we are the same company. <br/><br/>However, the updated website design should look more polished and convey high-quality products and services that we provide. <br/><br/>Our website is https://shopledgerslipsnet.paperformdepot.example/ if you want to take a look at our current website design. <br/><br/>we need 3 pages redesigned... <br/><br/>1. homepage:https://shopledgerslipsnet.paperformdepot.example/<br/><br/>2. Category page: <br/>https://shopledgerslipsnet.paperformdepot.example/order-computer-checks-c-4.html<br/><br/>3. Product detail page: https://shopledgerslipsnet.paperformdepot.example/voucher-computer-checks-p-35.html<br/><br/> I can provide many more pictures of our products if needed.<br/><br/><br/>BTW. I have another project here on mural hive, you can check the other ones too, so to make it easier to do both when working on this.<br/><br/> Please reach out to me should you have any questions or comments.
3 page
Designer to choose colors to be used in the design.

```html
<!DOCTYPE html>
<html lang="en">
<head>
<meta charset="utf-8">
<title>ShopLedgerSlips – Home</title>
<link href="https://fonts.googleapis.com/css2?family=Roboto:ital,wght@0,400;0,500;0,700;1,400&display=swap" rel="stylesheet">
<style>
:root{
  --green:#4c9a1f;
  --green-dark:#123f0b;
  --ink:#1f1f1f;
  --muted:#666;
  --line:#e2e2e2;
  --soft:#f0f0f0;
  --footer:#2a2c2e;
}
*{margin:0;padding:0;box-sizing:border-box}
html,body{width:1200px;height:3365px;overflow:hidden}
body{font-family:'Roboto',sans-serif;color:var(--ink);background:#fff;position:relative}
.abs{position:absolute}
.topbar{top:0;left:0;width:1200px;height:33px;background:#f2f2f2;font-size:15px}
.topbar .mail{left:112px;top:8px}
.topbar .social{left:792px;top:11px;display:flex;gap:14px}
.topbar .social span{width:12px;height:12px;border-radius:50%;background:#333}
.topbar .sep{left:914px;top:0;width:1px;height:33px;background:#999}
.topbar .login{left:960px;top:7px;font-weight:500}
.header{top:33px;left:0;width:1200px;height:74px;background:var(--green-dark)}
.brand{left:112px;top:24px;color:#8fd14f;font-weight:700;font-size:23px;display:flex;align-items:center;gap:8px}
.brand i{width:14px;height:14px;border-radius:50%;background:#8fd14f;display:block}
.search{left:595px;top:16px;width:295px;height:42px;background:#fff;border-radius:21px;font-size:12px;color:#777;padding:14px 20px}
.search b{position:absolute;right:4px;top:4px;width:34px;height:34px;border-radius:50%;background:var(--green)}
.cart{left:955px;top:16px;color:#fff;font-size:13px;font-weight:700;line-height:18px;padding-left:54px}
.cart:before{content:"";position:absolute;left:0;top:0;width:42px;height:42px;border-radius:50%;background:#fff}
.cart small{font-weight:400;font-size:12px}.cart em{font-style:normal;color:#8fd14f;font-weight:400}
.nav{top:107px;left:0;width:1200px;height:49px;background:#f4f4f4;border-bottom:1px solid var(--line);display:flex;gap:23px;padding:16px 0 0 117px;font-size:15px;font-weight:500}
.nav .on{color:var(--green);border-bottom:2px solid var(--green);height:23px}
.hero{top:156px;left:0;width:1200px;height:487px;background:linear-gradient(100deg,#c9b9a8 0%,#e8e1d8 40%,#b8a48c 100%)}
.hero h1{position:absolute;right:112px;top:132px;font-size:41px;font-weight:700;color:#fff}
.hero h1 span{color:var(--green)}
.hero p{position:absolute;right:112px;top:208px;color:#fff;font-size:17px}
.hero .find{position:absolute;left:700px;top:253px;width:387px;height:40px;background:#fff;border-radius:20px;font-size:13px;color:#555;padding:12px 8px}
.hero .find b{position:absolute;right:0;top:0;width:102px;height:40px;border-radius:20px;background:var(--green);color:#fff;font-size:15px;text-align:center;line-height:40px}
.h2{position:absolute;left:0;width:1200px;text-align:center;font-size:30px;font-weight:700;text-transform:uppercase}
.h2 span{color:var(--green)}
.card{position:absolute;width:304px;height:329px;border:1px solid var(--line);background:#fafafa;padding:18px 14px}
.card .ph{height:162px}
.card .inner{background:#fff;height:291px}
.card h3{text-align:center;font-weight:500;font-size:19px;padding-top:14px}
.card .sub{text-align:center;color:var(--green);font-size:15px;margin-top:9px}
.card .desc{text-align:center;color:var(--muted);font-size:14px;line-height:22px;margin-top:9px;padding:0 6px}
.card ul{list-style:none;margin:12px 0 0 38px;font-size:14px;color:var(--muted);line-height:25px}
.card li:before{content:"";display:inline-block;width:11px;height:11px;border-radius:50%;background:var(--green);margin-right:10px}
.welcome{top:1545px;left:0;width:1200px;height:366px;background:#efefef}
.welcome .ph{left:0;top:0;width:527px;height:366px;background:linear-gradient(120deg,#e0ddd6,#9fb8d6 60%,#556f8f)}
.welcome h2{position:absolute;left:600px;top:42px;font-size:26px;font-weight:700}
.welcome h2 span{color:var(--green)}
.welcome p{position:absolute;left:600px;top:94px;width:489px;font-size:15px;line-height:26.5px;color:var(--muted);text-align:justify}
.welcome a{position:absolute;left:600px;top:277px;width:161px;height:45px;border-radius:23px;background:var(--green);color:#fff;font-weight:700;font-size:14px;line-height:45px;text-align:center}
.arrow{position:absolute;width:14px;height:22px}
.lay{position:absolute;top:2049px;width:233px;height:263px;border:1px solid var(--line);background:#f7f7f7;padding:13px}
.lay .inner{background:#fff;height:235px;text-align:center}
.lay .ph{width:100px;height:118px;margin:0 auto;position:relative;top:12px;background:linear-gradient(#dfe8f3,#c6d7ea)}
.lay h4{font-size:15px;font-weight:500;line-height:21px;margin-top:30px;padding:0 8px}
.lay .pr{font-size:15px;color:var(--muted);margin-top:8px}.lay .pr b{color:var(--green)}
.save{left:1046px;top:2017px;width:58px;height:58px;border-radius:50%;background:var(--green);color:#fff;font-weight:700;font-size:15px;text-align:center;padding-top:10px;line-height:20px}
.testi{top:2394px;left:0;width:1200px;height:355px;background:#efefef}
.quote{position:absolute;width:300px;text-align:center}
.quote p{font-style:italic;color:var(--muted);font-size:14px;line-height:24px}
.quote .stars{color:#f39c12;font-size:16px;letter-spacing:3px;margin-top:12px}
.quote .who{font-size:16px;font-weight:500;margin-top:8px}
.quote .who i{display:inline-block;width:10px;height:10px;border-radius:50%;background:var(--green);margin-right:6px}
.quote .date{font-size:14px;color:var(--muted);margin-top:7px}
.soft{position:absolute;top:2899px;width:173px;height:71px;background:#fff;box-shadow:0 1px 6px rgba(0,0,0,.12);display:flex;align-items:center;justify-content:center;font-size:20px;font-weight:700;color:#444}
.footer{top:3049px;left:0;width:1200px;height:316px;background:var(--footer);color:#fff}
.fcol{position:absolute;top:69px;font-size:14px}
.fcol h5{font-size:17px;font-weight:500;margin-bottom:18px}
.fcol li{list-style:none;margin-bottom:14px}
.fcol li:before{content:"»";margin-right:10px}
.fcol .row{display:flex;gap:12px;margin-bottom:12px;line-height:20px}
.fcol .row i{width:10px;height:10px;border-radius:50%;border:2px solid #fff;flex:none;margin-top:5px}
.fcol small{font-size:12px}
.footer .rule{left:112px;top:259px;width:976px;height:1px;background:#555}
.footer .copy{left:0;top:276px;width:1200px;text-align:center;font-size:15px}
.footer .safe{left:112px;top:277px;width:74px;height:18px;border-radius:4px;background:#3c8a17}
.pay{top:276px;left:938px;display:flex;gap:4px}
.pay span{width:38px;height:20px;background:#fff;color:#234;font-size:9px;font-weight:700;text-align:center;line-height:20px}
.footer .code{left:1158px;top:280px;font-size:11px}
</style>
</head>
<body>

<div class="abs topbar">
  <div class="abs mail">✉ info@ledgerslipprinting.example</div>
  <div class="abs social"><span></span><span></span><span></span></div>
  <div class="abs sep"></div>
  <div class="abs login">Login / Register</div>
</div>

<div class="abs header">
  <div class="abs brand"><i></i>ShopLedgerSlips</div>
  <div class="abs search">Search By Software Checks<b></b></div>
  <div class="abs cart">MY CART<br><small>0 item- <em>$0.00</em></small></div>
</div>

<div class="abs nav">
  <span class="on">Home</span><span>About Us</span><span>Business Checks</span><span>Computer Checks</span><span>LedgerBooks Checks</span><span>Accessories</span><span>Reorder</span><span>Conact Us</span><span>Order Status</span>
</div>

<div class="abs hero" role="img" aria-label="Photo of a woman at a desk reviewing business checks">
  <h1><span>ORDER</span> BUSINESS <span>CHECKS</span></h1>
  <p>We are a blank check stock supplier for small and midsize</p>
  <div class="find">Checks by software &nbsp;&nbsp;&nbsp;&nbsp;&nbsp;&nbsp;&nbsp;&nbsp;&nbsp;&nbsp;&nbsp;&nbsp;&nbsp;&nbsp;&nbsp;&nbsp;&nbsp;▾<b>SEARCH</b></div>
</div>

<div class="h2" style="top:716px">Featured <span>Checks</span></div>

<div class="card" style="left:111px;top:781px"><div class="inner"><div class="ph" role="img" aria-label="Computer check samples" style="background:linear-gradient(#dde4ee,#bccbe0)"></div><h3>Computer Checks</h3><ul><li>100% software Compatible</li><li>Ships within 24hr</li><li>Free logo</li></ul></div></div>
<div class="card" style="left:447px;top:781px"><div class="inner"><div class="ph" role="img" aria-label="Manual check book samples" style="background:linear-gradient(#e2e7ef,#c3cfe0)"></div><h3>Manual Checks</h3><ul><li>Fits for 7 ring binder</li><li>Ships within 24hr</li><li>Free logo</li></ul></div></div>
<div class="card" style="left:783px;top:781px"><div class="inner"><div class="ph" role="img" aria-label="LedgerBooks check product image" style="background:linear-gradient(#e9a320,#1f6f8b)"></div><h3>LedgerBooks Checks</h3><div class="sub">Voucher Checks - 3 Per Page - wallet</div><div class="desc">Order custom designed LedgerBooks checks for any size business.</div></div></div>
<div class="card" style="left:111px;top:1134px"><div class="inner"><div class="ph" role="img" aria-label="Quickfin checks product box" style="background:linear-gradient(120deg,#e8e0c8,#c8251f 50%,#e08a1e)"></div><h3>Quickfin Checks</h3><div class="sub">Top Check - 3 on Page - wallet</div><div class="desc">Cheap Quickfin Checks, Highest Quality Quickfin checks for Less.</div></div></div>
<div class="card" style="left:447px;top:1134px"><div class="inner"><div class="ph" role="img" aria-label="Deposit slips with a pen on a wooden desk" style="background:linear-gradient(120deg,#6b4528,#d8d6d2 50%,#5a3a22)"></div><h3>Deposit Slips</h3><div class="sub">Manual &amp; Computer Deposit Slips</div><div class="desc">Manual &amp; Computer deposit slips Avail. in single copy, duplicates, &amp; triplicates.</div></div></div>
<div class="card" style="left:783px;top:1134px"><div class="inner"><div class="ph" role="img" aria-label="Hand pressing a self-inking stamp" style="background:linear-gradient(#f2f2f2,#c9c2b8 60%,#3a3a3a)"></div><h3>Check Accessories</h3><div class="sub">Self-Inking Stamps - Envelopes</div><div class="desc">Browse our fine selection of Check envelopes &amp; self-inking check stamps.</div></div></div>

<div class="abs welcome">
  <div class="abs ph" role="img" aria-label="Photo of a woman working on a laptop at a kitchen table"></div>
  <h2>WELCOME TO <span>SHOP LEDGER SLIPS</span></h2>
  <p>Welcome to the online ordering system of ShopLedgerSlips.example, online ordering at Shop Ledger Slips provides the most Comprehensive business check experience and selection available online, including traditional Manual desktop checks used with the 7 ring check binder, and an extensive selection of computer checks. Our computer checks are available in many layout styles and colors,</p>
  <a>LEARN MORE ➜</a>
</div>

<div class="h2" style="top:1986px">Checks by <span>Layout</span></div>
<svg class="arrow" style="left:44px;top:2162px" viewBox="0 0 14 22"><path d="M11 2L3 11l8 9" fill="none" stroke="#333" stroke-width="3"/></svg>
<svg class="arrow" style="left:1134px;top:2162px" viewBox="0 0 14 22"><path d="M3 2l8 9-8 9" fill="none" stroke="#333" stroke-width="3"/></svg>
<div class="lay" style="left:111px"><div class="inner"><div class="ph" role="img" aria-label="Voucher check layout"></div><h4>LedgerBooks Voucher Checks</h4><div class="pr">From <b>$12.99</b></div></div></div>
<div class="lay" style="left:359px"><div class="inner"><div class="ph" role="img" aria-label="3 per page check layout"></div><h4>Blank Tallyware LedgerBooks 3 Per Page Check</h4><div class="pr">From <b>$9.99</b></div></div></div>
<div class="lay" style="left:607px"><div class="inner"><div class="ph" role="img" aria-label="High security voucher check layout"></div><h4>Blank High Security Voucher Checks</h4><div class="pr">From <b>$14.99</b></div></div></div>
<div class="lay" style="left:853px"><div class="inner"><div class="ph" role="img" aria-label="Wallet check layout"></div><h4>wallet LedgerBooks Checks</h4><div class="pr">From <b>$13.99</b></div></div></div>
<div class="abs save">Save<br>10%</div>

<div class="abs testi">
  <div class="h2" style="top:46px">What our <span>Customers say</span></div>
  <svg class="arrow" style="left:44px;top:183px" viewBox="0 0 14 22"><path d="M11 2L3 11l8 9" fill="none" stroke="#333" stroke-width="3"/></svg>
  <svg class="arrow" style="left:1134px;top:183px" viewBox="0 0 14 22"><path d="M3 2l8 9-8 9" fill="none" stroke="#333" stroke-width="3"/></svg>
  <div class="quote" style="left:111px;top:111px"><p>A great place to shop for business checks and envelopes. Customer service is A+ the checks arived today, it works fine with our tallyware bookkeeping software, the same with the window envelopes.</p><div class="stars">★★★★★</div><div class="who"><i></i>Jana &nbsp;| &nbsp;<i></i>Portland</div><div class="date">03/23/2008</div></div>
  <div class="quote" style="left:450px;top:111px"><p>Local company that was able to deliver the checks to me quickly at a resinable price. They even called to correct a discrepancy from our side. The checks I ordered has came just on time..</p><div class="stars">★★★★★</div><div class="who"><i></i>Marlon &nbsp;| &nbsp;<i></i>Atlanta, GA</div><div class="date">06/16/2008</div></div>
  <div class="quote" style="left:787px;top:124px"><p>This geys are simply the best. the checks are nice and clean, the price is great and procecing and shipping is fast 5 stars I will do business again. :)</p><div class="stars" style="margin-top:22px">★★★★★</div><div class="who"><i></i>Rosalyn &nbsp;| &nbsp;<i></i>Tulare, CA</div><div class="date">09/19/2008</div></div>
</div>

<div class="h2" style="top:2827px">Checks by <span>Software</span></div>
<svg class="arrow" style="left:44px;top:2924px" viewBox="0 0 14 22"><path d="M11 2L3 11l8 9" fill="none" stroke="#333" stroke-width="3"/></svg>
<svg class="arrow" style="left:1134px;top:2924px" viewBox="0 0 14 22"><path d="M3 2l8 9-8 9" fill="none" stroke="#333" stroke-width="3"/></svg>
<div class="soft" style="left:111px">Sagewood</div>
<div class="soft" style="left:312px">Quickfin</div>
<div class="soft" style="left:513px">Plumgrove</div>
<div class="soft" style="left:714px">Northsoft Ledger</div>
<div class="soft" style="left:915px">TitleDesk</div>

<div class="abs footer">
  <div class="fcol" style="left:111px"><h5>Info</h5><ul><li>Contact us</li><li>Order History</li><li>Track Order</li><li>Help &amp; Support</li></ul></div>
  <div class="fcol" style="left:362px;width:260px"><h5>Contact Us</h5>
    <div class="row"><i></i><span>Ledger Slip Printing 14 Alder Court Maple Hollow, NY 10980</span></div>
    <div class="row" style="margin-top:16px"><i></i><span>1-800-555-0142</span></div>
    <div class="row" style="margin-top:16px"><i></i><span>info@ledgerslipprinting.example</span></div></div>
  <div class="fcol" style="left:711px"><h5>Opening Hours</h5>
    <div class="row"><i></i><span>Monday - Tue<br><small>9:30 a.m. - 5 p.m. EST</small></span></div>
    <div class="row"><i></i><span>Normal Sessions<br><small>9:30 a.m. - 1 p.m. EST</small></span></div>
    <div class="row"><i></i><span>Saturday - Sunday | Closed</span></div></div>
  <div class="fcol" style="left:966px"><h5>Information</h5><ul><li>About Us</li><li>Terms of Use</li><li>Privacy Policy</li><li>Disclaimer</li></ul></div>
  <div class="abs rule"></div>
  <div class="abs safe"></div>
  <div class="abs copy">© 2019 Shop Ledger Slips. All Rights Reserved</div>
  <div class="abs pay"><span>Cardo</span><span>Payline</span><span>Tendr</span><span>Coinra</span></div>
  <div class="abs code">C37</div>
</div>

</body>
</html>
```